VOMRA Pty Ltd Business Card

Looking for a simple yet eye-catching double-sided business card design using my company logo on one side and contact details on the other.

Target Market(s)

Government

Industry/Entity Type

Communication Systems Engineering

Contact Information for Business Card

VOMRA Pty Ltd

Requirements
Nice to have
• Would be great to have a QR code so details can be scanned into contacts

```html
<!DOCTYPE html>
<html lang="en">
<head>
<meta charset="utf-8">
<title>VOMRA Pty Ltd Business Card</title>
<link href="https://fonts.googleapis.com/css2?family=Arimo:wght@400;700&display=swap" rel="stylesheet">
<style>
  :root {
    --backdrop: #2a2a2b;
    --card: #2f363d;
    --card-edge: #3a424a;
    --ink: #ffffff;
    --ink-soft: #d9dde1;
    --paper: #f4f5f5;
  }
  * { margin: 0; padding: 0; box-sizing: border-box; }
  html, body {
    width: 1200px; height: 689px; overflow: hidden;
    background: var(--backdrop);
    font-family: "Arimo", Arial, sans-serif;
    color: var(--ink);
  }
  .stage {
    position: relative; width: 1200px; height: 689px;
    display: flex; align-items: center; justify-content: center; gap: 60px;
  }
  .card {
    position: relative; width: 520px; height: 300px;
    background: var(--card);
    border-radius: 22px;
    overflow: hidden;
    box-shadow: 0 18px 40px rgba(0,0,0,.45);
  }
  /* Front */
  .card-front {
    display: flex; align-items: center; justify-content: center; gap: 18px;
  }
  .brand-dot {
    width: 18px; height: 18px; border-radius: 50%;
    background: var(--ink);
  }
  .brand-name {
    font-weight: 700; font-size: 62px; letter-spacing: 2px;
    color: var(--ink); line-height: 1;
  }
  /* Back */
  .card-back { padding: 44px 0 0 44px; }
  .circuit-art {
    position: absolute; top: 0; right: 0; width: 54%; height: 100%;
    background: linear-gradient(110deg, var(--card) 0%, #59626b 35%, #c9cdd0 62%, var(--paper) 100%);
  }
  .back-brand {
    font-weight: 700; font-size: 40px; letter-spacing: 1.5px; line-height: 1;
  }
  .person { margin-top: 38px; }
  .person-name { font-weight: 700; font-size: 20px; }
  .person-role { font-size: 12px; color: var(--ink-soft); margin-top: 3px; }
  .address { margin-top: 22px; font-size: 13px; line-height: 1.4; color: var(--ink-soft); }
  .contacts { list-style: none; margin-top: 18px; font-size: 13px; line-height: 1.45; color: var(--ink-soft); }
  .contacts li { display: flex; align-items: center; gap: 9px; }
  .contacts svg { width: 11px; height: 11px; fill: var(--ink); flex: none; }
</style>
</head>
<body>
<main class="stage">
  <section class="card card-front" aria-label="Business card front">
    <span class="brand-dot"></span>
    <span class="brand-name">VOMRA</span>
  </section>

  <section class="card card-back" aria-label="Business card back">
    <div class="circuit-art" role="img" aria-label="Circuit-board tree illustration in white and slate"></div>
    <div class="back-brand">VOMRA</div>
    <div class="person">
      <div class="person-name">Daniel Morgan</div>
      <div class="person-role">Managing Director</div>
    </div>
    <div class="address">4216 Willow Bend Road<br>Darwin, Territory 58210</div>
    <ul class="contacts">
      <li><svg viewBox="0 0 24 24"><path d="M6.6 10.8a15.1 15.1 0 0 0 6.6 6.6l2.2-2.2c.3-.3.7-.4 1-.2 1.1.4 2.3.6 3.6.6.6 0 1 .4 1 1V20c0 .6-.4 1-1 1A17 17 0 0 1 3 4c0-.6.4-1 1-1h3.5c.6 0 1 .4 1 1 0 1.3.2 2.5.6 3.6.1.3 0 .7-.2 1z"/></svg>555-210-4387</li>
      <li><svg viewBox="0 0 24 24"><path d="M2 5h20v14H2zM4 7v.5l8 5 8-5V7l-8 5z"/></svg>info@vomra.org</li>
      <li><svg viewBox="0 0 24 24"><circle cx="12" cy="12" r="10"/></svg>www.vomra.org</li>
    </ul>
  </section>
</main>
</body>
</html>
```